Banner ads for LP that work with same theme as below banners

Love the banner ads below. Need more with attached photos. But use the same wording, font as in below banner ads. Should be LP size 1200/627 so I can use for Pixorly and LP. Looking for great ads to use as LP ads. We do lots of ads so it will be worth your time to enter this contest you will be rewarded with a ton of work. Need several banner ads that work together. So maybe 1 of the dresses, 1 of the sweater, 1 of the leggings, 1 of the jacket

Target Market(s)

Women 24-45

Industry/Entity Type

Fashion

Requirements
Must have
• Banner ads that work for LP and Pixorly
Nice to have
• Several options to choose from
Should not have
• not sure

```html
<!DOCTYPE html>
<html lang="en">
<head>
<meta charset="UTF-8">
<title>Our Best Dresses Ever – Banner</title>
<link rel="stylesheet" href="https://fonts.googleapis.com/css2?family=Yellowtail&family=Tinos:wght@400;700&display=swap">
<style>
  :root {
    --night: #161616;
    --charcoal: #242424;
    --slate: #6b6b6b;
    --slate-light: #7a7a7a;
    --cream: #e4e0d8;
    --white: #ffffff;
    --title-grey: #7a7876;
    --glow: rgba(190, 120, 70, 0.35);
  }
  html, body {
    margin: 0;
    padding: 0;
    overflow: hidden;
    background: var(--night);
  }
  .banner {
    position: relative;
    width: 1200px;
    height: 627px;
    overflow: hidden;
    background: var(--night);
  }
  .banner__backdrop {
    position: absolute;
    inset: 0;
  }
  .headline {
    position: absolute;
    left: 170px;
    top: 22px;
    margin: 0;
    display: flex;
    align-items: baseline;
    white-space: nowrap;
    font-weight: 400;
  }
  .headline__script {
    font-family: "Yellowtail", cursive;
    font-size: 76px;
    color: var(--white);
    line-height: 1;
  }
  .headline__product {
    font-family: "Tinos", "Times New Roman", serif;
    font-weight: 700;
    font-size: 50px;
    letter-spacing: 13px;
    color: var(--title-grey);
    margin: 0 6px 0 26px;
  }
  .product {
    position: absolute;
    border-radius: 50%;
    border: 4px solid var(--white);
    box-sizing: border-box;
  }
  .product--sweater-rust {
    left: 82px; top: 140px; width: 264px; height: 240px;
    background: radial-gradient(circle at 55% 60%, #b5523f 0%, #a4483a 38%, #e9e4e2 62%);
  }
  .product--sweater-lilac {
    left: 463px; top: 155px; width: 264px; height: 248px;
    background: radial-gradient(circle at 50% 65%, #c9c8dc 0%, #b9b8cf 40%, #f0eef0 66%);
  }
  .product--lace-dress {
    left: 863px; top: 166px; width: 264px; height: 256px;
    background: radial-gradient(circle at 50% 60%, #2f4f78 0%, #3a3350 40%, #e8e6e8 66%);
  }
  .cta {
    position: absolute;
    left: 720px;
    top: 507px;
    margin: 0;
    font-family: "Tinos", "Times New Roman", serif;
    font-size: 38px;
    color: var(--white);
    letter-spacing: 0.5px;
    font-weight: 400;
  }
  .cta strong { font-weight: 700; }
</style>
</head>
<body>
  <div class="banner">
    <svg class="banner__backdrop" width="1200" height="627" viewBox="0 0 1200 627" aria-hidden="true">
      <defs>
        <linearGradient id="slateBand" x1="0" y1="0" x2="0" y2="1">
          <stop offset="0" stop-color="#7a7a7a"/>
          <stop offset="1" stop-color="#5a5a5a"/>
        </linearGradient>
        <radialGradient id="warmGlow" cx="0.47" cy="0.22" r="0.35">
          <stop offset="0" stop-color="var(--glow)"/>
          <stop offset="1" stop-color="rgba(0,0,0,0)"/>
        </radialGradient>
      </defs>
      <rect width="1200" height="627" fill="var(--night)"/>
      <rect width="1200" height="627" fill="url(#warmGlow)"/>
      <path class="band band--main" d="M0 138 C 300 150, 700 155, 1200 95 L1200 600 C 800 590, 300 570, 0 555 Z" fill="url(#slateBand)"/>
      <path class="band band--lower" d="M0 445 C 400 440, 800 470, 1200 495 L1200 600 C 800 590, 300 575, 0 558 Z" fill="var(--slate-light)"/>
      <path class="band band--cream" d="M0 418 C 350 405, 800 440, 1200 462 L1200 494 C 800 470, 400 440, 0 446 Z" fill="var(--cream)"/>
    </svg>

    <h1 class="headline">
      <span class="headline__script">Our Best</span>
      <span class="headline__product">DRESSES</span>
      <span class="headline__script">Ever!</span>
    </h1>

    <div class="product product--sweater-rust" role="img" aria-label="Model wearing a rust lace-up knit sweater dress"></div>
    <div class="product product--sweater-lilac" role="img" aria-label="Model wearing a lilac turtleneck knit sweater dress"></div>
    <div class="product product--lace-dress" role="img" aria-label="Model wearing a navy and blue floral lace mini dress"></div>

    <p class="cta"><strong>SHOP</strong> THE <strong>LOOK</strong></p>
  </div>
</body>
</html>
```